Smile club flyer design

I am launching an office smile club and would like a design that sits my branding and that is appealing to customers. I have a design (I need a new one) that has all the information.
My website is maplehavendentalcarekx.com
Brand color is green. The design can be any color

Target Market(s)

Ages 30+

Industry/Entity Type

Dental

Font styles to use
Serif

Requirements
Must have
• Appealing to patients

```html
<!DOCTYPE html>
<html lang="en">
<head>
<meta charset="utf-8">
<title>Smile Club Membership Flyer</title>
<link href="https://fonts.googleapis.com/css2?family=Playfair+Display:wght@700;800&family=Great+Vibes&family=Montserrat:wght@800&family=Poppins:wght@400;500;600;700&family=Archivo+Black&display=swap" rel="stylesheet">
<style>
  :root{
    --backdrop:#f1f4f2;
    --mint:#e4f8ee;
    --mint-deep:#c9efdd;
    --brand-green:#1a8a45;
    --teal:#17b3a1;
    --teal-mid:#10968a;
    --teal-dark:#0c5a4e;
    --card:#b3ebe6;
    --navy:#0a3358;
    --ink:#111;
    --red:#d8140f;
    --leaf:#a8d9b8;
  }
  *{box-sizing:border-box;margin:0;padding:0}
  html,body{width:960px;height:1200px;overflow:hidden;background:var(--backdrop)}
  .flyer{position:absolute;left:80px;top:0;width:800px;height:1200px;overflow:hidden;
    background:radial-gradient(ellipse at 80% 5%,var(--mint-deep),transparent 45%),
               radial-gradient(ellipse at 10% 70%,#d7f5e6,transparent 50%),
               linear-gradient(180deg,var(--mint) 0%,#f2fcf7 45%,var(--mint) 100%);
    font-family:"Poppins",sans-serif;color:var(--ink)}
  .abs{position:absolute}
  .foliage{position:absolute;border-radius:50%;opacity:.55;
    background:radial-gradient(ellipse,var(--leaf) 0%,rgba(168,217,184,0) 70%)}
  .foliage-top{left:-40px;top:-20px;width:260px;height:260px}
  .foliage-right{left:690px;top:320px;width:150px;height:230px}
  .foliage-bottom{left:290px;top:1000px;width:220px;height:200px}

  .brand{left:0;width:800px;top:62px;text-align:center;color:var(--brand-green);
    font-family:"Playfair Display",serif;font-weight:700}
  .brand-name{font-size:56px;line-height:56px}
  .brand-sub{font-size:24px;letter-spacing:7px;line-height:30px;margin-top:8px}
  .brand-sub::before,.brand-sub::after{content:"";display:inline-block;width:30px;height:3px;background:var(--brand-green);vertical-align:middle;margin:0 8px}

  .intro{left:0;width:800px;top:170px;text-align:center;font-family:"Great Vibes",cursive;font-size:96px;line-height:110px;color:var(--navy)}
  .club{left:0;width:800px;top:256px;text-align:center;font-family:"Playfair Display",serif;font-weight:800;font-size:92px;line-height:100px;color:var(--teal)}
  .membership{left:0;width:800px;top:350px;text-align:center;font-family:"Montserrat",sans-serif;font-weight:800;font-size:55px;letter-spacing:3px;line-height:60px;color:var(--navy)}
  .tagline{left:0;width:800px;top:413px;text-align:center;font-size:25px;font-weight:500;line-height:36px}

  .plan{position:absolute;top:485px;width:226px;height:341px}
  .plan-tab{position:absolute;left:16px;top:0;width:188px;height:72px;border-radius:30px 30px 0 0;color:#fff;text-align:center;padding-top:14px}
  .plan-tab .tier{font-family:"Playfair Display",serif;font-weight:700;font-size:23px;line-height:24px}
  .plan-tab .focus{font-size:18px;line-height:24px;color:#d6f5ef;font-weight:500}
  .fold{position:absolute;top:56px;width:0;height:0;border-bottom:15px solid}
  .fold-l{left:0;border-left:16px solid transparent}
  .fold-r{right:0;border-right:16px solid transparent}
  .plan-body{position:absolute;left:0;top:71px;width:226px;height:270px;background:var(--card);border-radius:0 0 24px 24px}
  .price{text-align:center;font-family:"Playfair Display",serif;font-weight:800;font-size:52px;line-height:56px;color:var(--teal-dark);margin-top:6px}
  .per{text-align:center;font-size:18px;font-weight:500;line-height:22px;margin-top:2px}
  .perks{list-style:none;margin:18px 0 0 20px;width:196px}
  .perks li{position:relative;padding-left:14px;font-size:14px;line-height:17px;margin-bottom:9px}
  .perks li::before{content:"";position:absolute;left:0;top:5px;width:8px;height:8px;border-radius:50%;background:var(--teal)}
  .core{left:49px}.core .plan-tab{background:var(--teal)}.core .fold{border-bottom-color:#0e8a7c}
  .bright{left:288px}.bright .plan-tab{background:var(--teal-mid)}.bright .fold{border-bottom-color:#0a6d62}
  .total{left:528px}.total .plan-tab{background:var(--teal-dark)}.total .fold{border-bottom-color:#06372f}

  .join{left:61px;top:860px;font-family:"Playfair Display",serif;font-weight:800;font-size:26px;line-height:34px;color:var(--teal)}
  .phone{left:61px;top:893px;display:flex;align-items:center;gap:12px;font-size:37px;font-weight:500;line-height:46px}
  .rule{left:61px;width:384px;height:1px;background:#9aa}
  .financing{left:61px;top:960px;font-family:"Archivo Black",sans-serif;font-size:19px;line-height:26px}
  .lenders{left:61px;top:991px;display:flex;gap:28px;align-items:center;font-size:26px;font-weight:600;line-height:34px;color:#2a3a44}
  .lenders span{display:flex;align-items:center;gap:7px}
  .lenders i{display:inline-block;width:14px;height:14px;border-radius:50%;background:var(--teal)}
  .plans{left:61px;top:1045px;font-family:"Archivo Black",sans-serif;font-size:19px;line-height:26px;color:var(--navy)}
  .fine{left:61px;top:1074px;font-size:10px;line-height:14px}

  .refresh{left:517px;top:868px;width:226px;height:261px}
  .refresh .plan-tab{left:20px;width:189px;height:74px;background:var(--navy);padding-top:15px}
  .refresh .plan-tab .focus{color:#fff;font-size:17px}
  .refresh .fold{border-bottom-color:#06203a;top:59px}
  .refresh .plan-body{top:73px;height:188px;background:var(--teal);border-radius:0 0 22px 22px}
  .refresh .price{color:#fff;margin-top:6px}
  .refresh .perks{margin:6px 0 0 30px}
  .refresh .perks li{color:#fff;font-size:14px;line-height:19px}
  .refresh .perks li::before{background:var(--teal-dark)}
  .offer{position:absolute;left:23px;top:137px;width:180px;height:32px;border-radius:7px;background:var(--red);color:#fff;text-align:center;font-family:"Archivo Black",sans-serif;font-size:16px;line-height:32px}
  .burst{left:490px;top:850px}

  .band{left:0;top:1179px;width:800px;height:21px;background:var(--teal)}
</style>
</head>
<body>
<main class="flyer">
  <div class="foliage foliage-top" role="img" aria-label="Soft watercolour green leaves"></div>
  <div class="foliage foliage-right" role="img" aria-label="Soft watercolour green leaves"></div>
  <div class="foliage foliage-bottom" role="img" aria-label="Soft watercolour green leaves"></div>

  <header class="abs brand">
    <div class="brand-name">Maplehaven</div>
    <div class="brand-sub">DENTAL CARE</div>
  </header>

  <div class="abs intro">Introducing</div>
  <h1 class="abs club">SMILE CLUB</h1>
  <div class="abs membership">MEMBERSHIP</div>
  <p class="abs tagline">Affordable dental care - No insurance required</p>

  <section class="plan core">
    <span class="fold fold-l"></span><span class="fold fold-r"></span>
    <div class="plan-tab"><div class="tier">CORE CARE</div><div class="focus">PREVENTIVE</div></div>
    <div class="plan-body">
      <div class="price">$39</div><div class="per">PER MONTH</div>
      <ul class="perks">
        <li>Comprehensive Annual Exam</li>
        <li>2 Professional Cleanings per Year</li>
        <li>Routine Bitewing X-rays</li>
        <li>10% Savings on Treatment</li>
      </ul>
    </div>
  </section>

  <section class="plan bright">
    <span class="fold fold-l"></span><span class="fold fold-r"></span>
    <div class="plan-tab"><div class="tier">BRIGHT</div><div class="focus">COSMETIC</div></div>
    <div class="plan-body">
      <div class="price">$59</div><div class="per">PER MONTH</div>
      <ul class="perks">
        <li>Annual In-Office Whitening</li>
        <li>Custom Whitening Trays</li>
        <li>15% Savings on Elective Treatment</li>
      </ul>
    </div>
  </section>

  <section class="plan total">
    <span class="fold fold-l"></span><span class="fold fold-r"></span>
    <div class="plan-tab"><div class="tier">TOTAL SMILE</div><div class="focus">PERIODONTAL</div></div>
    <div class="plan-body">
      <div class="price">$89</div><div class="per">PER MONTH</div>
      <ul class="perks">
        <li>3-4 Perio Maintenance</li>
        <li>1 Comprehensive Exam</li>
        <li>Diagnostic X-rays</li>
        <li>15% Savings on Restorative &amp; Elective Care</li>
      </ul>
    </div>
  </section>

  <h2 class="abs join">JOIN SMILE CLUB TODAY!</h2>
  <div class="abs phone">
    <svg width="34" height="34" viewBox="0 0 34 34" aria-hidden="true">
      <circle cx="17" cy="17" r="17" fill="#0f8a7c"/>
      <path d="M11 9c1-1 2-1 3 0l2 3c.5 1 .3 1.8-.5 2.5l-1 .8c.8 2 2.3 3.6 4.3 4.5l.8-1c.7-.8 1.6-1 2.5-.5l3 2c1 .7 1 1.8 0 2.8l-1.3 1.3c-1.5 1.5-4.5.8-7.8-2.3S8.3 12.5 9.8 10.4z" fill="#fff"/>
    </svg>
    865-555-0142
  </div>
  <div class="abs rule" style="top:948px"></div>
  <div class="abs financing">FLEXIBLE FINANCING FOR TREATMENT</div>
  <div class="abs lenders"><span><i></i>PayEase</span><span><i></i>Plumline</span></div>
  <div class="abs rule" style="top:1033px"></div>
  <div class="abs plans">PAYMENT PLANS AVAILABLE</div>
  <p class="abs fine">*$49 Lifetime Activation Fee (Non-Refundable)</p>

  <section class="plan refresh">
    <span class="fold fold-l"></span><span class="fold fold-r"></span>
    <div class="plan-tab"><div class="tier">SMILE</div><div class="focus">REFRESH PACKAGE</div></div>
    <div class="plan-body">
      <div class="price">$499</div>
      <ul class="perks"><li>Cleaning<br>+Comprehensive Exam<br>+ Whitening</li></ul>
      <div class="offer">Limited Time Offer</div>
    </div>
  </section>

  <svg class="abs burst" width="60" height="60" viewBox="0 0 60 60" aria-hidden="true">
    <polygon fill="#d8140f" points="30,0 35,11 46,4 45,17 58,16 50,27 60,34 48,38 53,50 40,47 36,60 30,50 24,60 20,47 7,50 12,38 0,34 10,27 2,16 15,17 14,4 25,11"/>
    <text x="30" y="35" text-anchor="middle" fill="#fff" font-family="Poppins,sans-serif" font-weight="700" font-size="14">NEW</text>
  </svg>

  <div class="abs band"></div>
</main>
</body>
</html>
```